Need Business Card for our Real Estate Business with Sales Executive's Picture

PANTONE 484 C ( RED)

PANTONE 2766 C ( BLUE

Industry/Entity Type

Real Estate

Contact Information for Business Card

Name, Mobile, email, & picture of Person
Agency Phone, address, Web address

Requirements
Must have
• Our Logo Colours, Agent Picture,

```html
<!DOCTYPE html>
<html lang="en">
<head>
<meta charset="utf-8">
<title>Kestrel Realty – Business Card</title>
<link href="https://fonts.googleapis.com/css2?family=Cinzel:wght@400;500&family=Roboto:wght@400&display=swap" rel="stylesheet">
<style>
  :root {
    --navy: #0b1538;
    --maroon: #600b12;
    --paper: #f3f3f3;
    --ink: #4a4a4a;
    --white: #ffffff;
    --backdrop: #e6e6e6;
  }
  * { margin: 0; padding: 0; box-sizing: border-box; }
  html, body { width: 1200px; height: 960px; overflow: hidden; }
  body { background: var(--backdrop); position: relative; font-family: "Roboto", Arial, sans-serif; }

  .card { position: absolute; width: 600px; height: 343px; box-shadow: 0 2px 6px rgba(0,0,0,.25); overflow: hidden; }
  .card--front { left: 314px; top: 113px; background: var(--paper); }
  .card--back { left: 311px; top: 472px; background: var(--navy); }

  .brand-name { font-family: "Cinzel", Georgia, serif; font-weight: 500; letter-spacing: 1px; white-space: nowrap; }
  .card--front .brand-name { position: absolute; left: 30px; top: 118px; font-size: 36px; color: var(--navy); }
  .card--back .brand-name { position: absolute; left: 0; right: 0; top: 178px; text-align: center; font-size: 44px; color: var(--white); }

  .address { position: absolute; left: 30px; top: 195px; font-size: 14px; line-height: 19px; color: var(--ink); }
  .contact-list { position: absolute; left: 30px; top: 241px; list-style: none; }
  .contact-list li { display: flex; align-items: center; height: 19.5px; font-size: 14px; color: var(--ink); }
  .contact-list svg { width: 13px; height: 13px; margin-right: 10px; fill: var(--navy); }

  .portrait { position: absolute; left: 352px; top: 15px; width: 244px; height: 275px;
    background: radial-gradient(ellipse at 45% 35%, #c49a7e 0 22%, transparent 23%),
                linear-gradient(180deg, #efefef 0%, #efefef 55%, #1d3a82 56%, #16306e 100%); }

  .front-bands { position: absolute; left: 0; top: 0; width: 600px; height: 343px; }
  .agent { position: absolute; left: 320px; right: 0; top: 290px; text-align: center; color: var(--white); font-family: "Cinzel", Georgia, serif; }
  .agent-name { font-size: 22px; font-weight: 400; line-height: 26px; }
  .agent-title { font-size: 15px; line-height: 20px; letter-spacing: .5px; }

  .back-web { position: absolute; left: 0; right: 0; top: 296px; text-align: center; color: var(--white); font-size: 14px; letter-spacing: 3.5px; }
</style>
</head>
<body>
  <section class="card card--front">
    <div class="brand-name">Kestrel Realty</div>

    <p class="address">214 Alder Court<br>Juneau, Alaska 99801</p>

    <ul class="contact-list">
      <li><svg viewBox="0 0 24 24"><path d="M6.6 10.8a15 15 0 0 0 6.6 6.6l2.2-2.2c.3-.3.7-.4 1-.2 1.1.4 2.3.6 3.6.6.6 0 1 .4 1 1V20c0 .6-.4 1-1 1A17 17 0 0 1 3 4c0-.6.4-1 1-1h3.5c.6 0 1 .4 1 1 0 1.3.2 2.5.6 3.6.1.3 0 .7-.2 1z"/></svg>555 210 4837</li>
      <li><svg viewBox="0 0 24 24"><path d="M7 1h10a2 2 0 0 1 2 2v18a2 2 0 0 1-2 2H7a2 2 0 0 1-2-2V3a2 2 0 0 1 2-2zm0 3v14h10V4zm5 15.5a1 1 0 1 0 0 2 1 1 0 0 0 0-2z"/></svg>555 318 6624</li>
      <li><svg viewBox="0 0 24 24"><path d="M2 5h20v14H2zm2 2v.5l8 5 8-5V7zm0 2.8V17h16V9.8l-8 5z"/></svg>daniel@kestrelrealty.com</li>
      <li><svg viewBox="0 0 24 24"><path d="M12 2a10 10 0 1 0 0 20 10 10 0 0 0 0-20zm6.9 6h-3a15 15 0 0 0-1.3-3.9A8 8 0 0 1 18.9 8zM12 4c.9 1.2 1.5 2.6 1.9 4h-3.8c.4-1.4 1-2.8 1.9-4zM4.3 14a8 8 0 0 1 0-4h3.4a16 16 0 0 0 0 4zm.8 2h3a15 15 0 0 0 1.3 3.9A8 8 0 0 1 5.1 16zm3-8h-3a8 8 0 0 1 4.3-3.9C8.8 5.3 8.4 6.6 8.1 8zM12 20c-.9-1.2-1.5-2.6-1.9-4h3.8c-.4 1.4-1 2.8-1.9 4zm2.3-6H9.7a14 14 0 0 1 0-4h4.6a14 14 0 0 1 0 4zm.3 5.9c.6-1.2 1-2.5 1.3-3.9h3a8 8 0 0 1-4.3 3.9zm1.7-5.9a16 16 0 0 0 0-4h3.4a8 8 0 0 1 0 4z"/></svg>www.kestrelrealty.com</li>
    </ul>

    <div class="portrait" role="img" aria-label="Portrait photo of the sales executive in a navy suit"></div>

    <svg class="front-bands" viewBox="0 0 600 343" aria-hidden="true">
      <rect x="0" y="329" width="292" height="14" fill="var(--navy)"/>
      <polygon points="284,343 322,287 600,287 600,343" fill="var(--white)"/>
      <polygon points="290,343 326,288 600,288 600,343" fill="var(--maroon)"/>
    </svg>

    <div class="agent">
      <div class="agent-name">DANIEL REYES</div>
      <div class="agent-title">CEO/FOUNDER</div>
    </div>
  </section>

  <section class="card card--back">
    <div class="brand-name">Kestrel Realty</div>
    <p class="back-web">www.kestrelrealty.com</p>
  </section>
</body>
</html>
```